Northfield Builders Guild Business card

We are looking for a new business card design with photo included.
Our business is a nonprofit construction contractor membership organization. We offer business education, assist with business setup and licensing, provide safety training, and provide a member directory.
URL: www.builderslinkguild.org
Color code:
CMYK: 0 cyan, 42 magenta, 100 yellow, 0 black for Print.
Hexidecimal: #FF9900
RGB: R 255; G 153; B 0

```html
<!DOCTYPE html>
<html lang="en">
<head>
<meta charset="utf-8">
<title>Northfield Builders Guild – Business Card</title>
<link href="https://fonts.googleapis.com/css2?family=Montserrat:wght@500;800&display=swap" rel="stylesheet">
<style>
  :root{
    --orange:#FF9900;
    --charcoal:#323132;
    --white:#ffffff;
    --backdrop:#1c1c1c;
    --font:'Montserrat', Arial, sans-serif;
  }
  html,body{margin:0;padding:0;overflow:hidden;}
  body{width:1200px;height:1015px;background:var(--backdrop);font-family:var(--font);position:relative;}
  .card{position:absolute;left:220px;width:760px;height:434px;overflow:hidden;background:var(--charcoal);box-shadow:0 14px 30px rgba(0,0,0,.55);}
  .card--services{top:50px;}
  .card--contact{top:530px;}
  .card__shape{position:absolute;inset:0;}
  .brand{position:absolute;display:flex;align-items:center;gap:12px;color:var(--charcoal);font-weight:800;font-size:28px;line-height:1.05;text-transform:uppercase;letter-spacing:.5px;}
  .brand__dot{width:18px;height:18px;border-radius:50%;background:var(--orange);flex:none;}
  .card--services .brand{left:40px;top:160px;}
  .card--contact .brand{left:420px;top:115px;}
  .services{position:absolute;right:40px;top:95px;margin:0;padding:0;list-style:none;text-align:right;color:var(--white);font-weight:500;font-size:16px;letter-spacing:.5px;text-transform:uppercase;}
  .services li{margin-bottom:22px;line-height:1.3;}
  .services li::after{content:"";display:inline-block;width:8px;height:8px;border-radius:50%;background:var(--orange);margin-left:6px;vertical-align:3px;}
  .person{position:absolute;left:50px;top:70px;color:var(--white);}
  .person__name{margin:0;color:var(--orange);font-weight:800;font-size:28px;text-transform:uppercase;}
  .person__role{margin:2px 0 0;font-weight:500;font-size:16px;text-transform:uppercase;letter-spacing:.5px;}
  .contacts{list-style:none;margin:20px 0 0;padding:0;font-size:18px;font-weight:500;}
  .contacts li{display:flex;align-items:center;gap:10px;margin-bottom:6px;}
  .contacts .note{color:var(--orange);}
  .icon{width:24px;height:24px;flex:none;}
  .address{margin:20px 0 0;font-size:18px;font-weight:500;line-height:1.3;font-style:normal;}
  .web{position:absolute;left:120px;bottom:30px;color:var(--orange);font-size:20px;font-weight:500;}
</style>
</head>
<body>

<section class="card card--services">
  <svg class="card__shape" viewBox="0 0 760 434" aria-hidden="true">
    <circle cx="130" cy="200" r="270" fill="var(--white)"/>
    <path d="M174.3 -51.1 A255 255 0 0 1 257.5 420.8" fill="none" stroke="var(--orange)" stroke-width="5"/>
  </svg>
  <div class="brand"><span class="brand__dot"></span><span>Northfield<br>Builders Guild</span></div>
  <ul class="services">
    <li>Business Education</li>
    <li>Assist with business setup<br>and licensing</li>
    <li>Provide safety training</li>
    <li>Provide a member directory</li>
  </ul>
</section>

<section class="card card--contact">
  <svg class="card__shape" viewBox="0 0 760 434" aria-hidden="true">
    <circle cx="590" cy="150" r="240" fill="var(--white)"/>
    <path d="M513 -61.4 A225 225 0 0 0 629 371.6" fill="none" stroke="var(--orange)" stroke-width="5"/>
  </svg>
  <div class="brand"><span class="brand__dot"></span><span>Northfield<br>Builders Guild</span></div>

  <div class="person">
    <h1 class="person__name">Daniel Mercer</h1>
    <p class="person__role">Managing Director</p>
    <ul class="contacts">
      <li><svg class="icon" viewBox="0 0 24 24"><circle cx="12" cy="12" r="12" fill="var(--orange)"/><path d="M8 7l2 0 1 3-1.5 1a7 7 0 0 0 3.5 3.5l1-1.5 3 1 0 2a2 2 0 0 1-2 1A10 10 0 0 1 7 9a2 2 0 0 1 1-2z" fill="var(--white)"/></svg>(541) 555-0147 <span class="note">(Office)</span></li>
      <li><svg class="icon" viewBox="0 0 24 24"><circle cx="12" cy="12" r="12" fill="var(--orange)"/><rect x="8.5" y="6" width="7" height="12" rx="1.5" fill="none" stroke="var(--white)" stroke-width="1.6"/></svg>800-555-0193</li>
      <li><svg class="icon" viewBox="0 0 24 24"><circle cx="12" cy="12" r="12" fill="var(--orange)"/><rect x="9" y="6" width="6" height="4" fill="var(--white)"/><rect x="6.5" y="10" width="11" height="5" rx="1" fill="var(--white)"/><rect x="9" y="15" width="6" height="3" fill="var(--white)"/></svg>541.555.0162</li>
      <li><svg class="icon" viewBox="0 0 24 24"><circle cx="12" cy="12" r="12" fill="var(--orange)"/><rect x="6.5" y="8" width="11" height="8" fill="var(--white)"/><path d="M6.5 8l5.5 4.5L17.5 8" fill="none" stroke="var(--orange)" stroke-width="1.2"/></svg>support@nbguild.org</li>
    </ul>
    <address class="address">4820 Ridgeline Ave<br>Suite #210, Springfield<br>OR 97477</address>
  </div>
  <div class="web">www.builderslinkguild.org</div>
</section>

</body>
</html>
```